New Business Card Design Project

We require a business card design for Vexalund, a newly established Indian company.
Our focus is on the development, manufacturing, and export of a diverse array of pharmaceutical products on a global scale. The card should convey a professional appearance, as our primary markets are in Africa, China, and Southeast Asian nations.
We envision a two-sided business card, with the reverse side dedicated to a logo set against a solid color or an elegantly designed pattern. The corners should be rounded. We would appreciate seeing both horizontal and vertical design options. We trust the designer to utilize their expertise in creating this design.

The content for the business card is included in the attached Word file.

Target Market(s)

Our primary markets are in Africa, China, and Southeast Asian, Latin America, Maldives, Sri Lanka

Industry/Entity Type

Pharmaceutical Manufacturing and Export

Contact Information for Business Card

Colors

Designer to choose colors to be used in the design.

Requirements
Must have
• The reverse side of the business card features solely the logo along with the tagline, "Remedies of Life."
Should not have
• The logo should not exceed two instances, encompassing both the front and back sides of the card.

```html
<!DOCTYPE html>
<html lang="en">
<head>
<meta charset="utf-8">
<title>Vexalund Business Card</title>
<link rel="stylesheet" href="https://fonts.googleapis.com/css2?family=Montserrat:wght@600;700&family=Lato:wght@400&display=swap">
<style>
  :root {
    --backdrop: #4f555d;
    --brand-blue: #29a9e0;
    --accent-coral: #ef5f4d;
    --card-white: #ffffff;
    --ink: #1c1c1c;
  }
  html, body {
    margin: 0;
    padding: 0;
    width: 1200px;
    height: 1120px;
    overflow: hidden;
    background: var(--backdrop);
  }
  .canvas {
    position: relative;
    width: 1200px;
    height: 1120px;
  }
  .card {
    position: absolute;
    border-radius: 36px;
    box-shadow: 6px 10px 18px rgba(0, 0, 0, 0.35);
  }
  .card-back {
    left: 156px;
    top: 120px;
    width: 726px;
    height: 415px;
    background: var(--brand-blue);
  }
  .card-front {
    left: 323px;
    top: 607px;
    width: 701px;
    height: 400px;
    background: var(--card-white);
  }
  .brand-dot {
    position: absolute;
    border-radius: 50%;
  }
  .card-back .brand-dot {
    left: 329px;
    top: 140px;
    width: 60px;
    height: 60px;
    background: var(--card-white);
  }
  .brand-name {
    position: absolute;
    margin: 0;
    font-family: "Montserrat", sans-serif;
    font-weight: 700;
    line-height: 1;
    white-space: nowrap;
  }
  .card-back .brand-name {
    left: 206px;
    top: 245px;
    width: 341px;
    text-align: center;
    font-size: 66px;
    color: var(--card-white);
  }
  .brand-rule {
    position: absolute;
    left: 206px;
    top: 309px;
    width: 341px;
    height: 2px;
    background: var(--card-white);
  }
  .tagline {
    position: absolute;
    left: 206px;
    top: 333px;
    width: 321px;
    text-align: center;
    margin: 0;
    font-family: "Montserrat", sans-serif;
    font-weight: 700;
    font-size: 30px;
    line-height: 1;
    color: var(--card-white);
  }
  .identity {
    position: absolute;
    left: 45px;
    top: 111px;
    font-family: "Lato", sans-serif;
    color: var(--ink);
  }
  .identity-bar {
    position: absolute;
    left: 25px;
    top: 117px;
    width: 5px;
    height: 43px;
    background: var(--brand-blue);
  }
  .person-name {
    margin: 0;
    font-size: 29px;
    line-height: 36px;
    color: var(--brand-blue);
  }
  .person-role, .person-company {
    margin: 0;
    font-size: 19px;
    line-height: 25px;
  }
  .contact-list {
    list-style: none;
    margin: 0;
    padding: 0;
    position: absolute;
    left: 45px;
    top: 214px;
    font-family: "Lato", sans-serif;
    font-size: 17px;
    color: var(--ink);
  }
  .contact-list li {
    display: flex;
    align-items: center;
    height: 20px;
  }
  .contact-list svg {
    width: 15px;
    height: 15px;
    margin-right: 14px;
    fill: var(--accent-coral);
    flex: none;
  }
  .address {
    position: absolute;
    left: 46px;
    top: 284px;
    margin: 0;
    font-family: "Lato", sans-serif;
    font-style: normal;
    font-size: 17px;
    line-height: 20px;
    color: var(--ink);
  }
  .card-front .brand-dot {
    left: 472px;
    top: 127px;
    width: 60px;
    height: 60px;
    background: var(--brand-blue);
  }
  .card-front .brand-name {
    left: 356px;
    top: 243px;
    width: 293px;
    text-align: center;
    font-size: 57px;
    color: var(--brand-blue);
  }
</style>
</head>
<body>
<main class="canvas">
  <section class="card card-back" aria-label="Card reverse">
    <span class="brand-dot"></span>
    <h1 class="brand-name">Vexalund</h1>
    <span class="brand-rule"></span>
    <p class="tagline">Remedies of Life</p>
  </section>

  <section class="card card-front" aria-label="Card front">
    <span class="identity-bar"></span>
    <div class="identity">
      <h2 class="person-name">Rohan K. Vashist</h2>
      <p class="person-role">CEO</p>
      <p class="person-company">Vexalund</p>
    </div>
    <ul class="contact-list">
      <li>
        <svg viewBox="0 0 24 24" aria-hidden="true"><path d="M6.6 10.8a15.5 15.5 0 0 0 6.6 6.6l2.2-2.2a1 1 0 0 1 1-.25 11.4 11.4 0 0 0 3.6.57 1 1 0 0 1 1 1V20a1 1 0 0 1-1 1A17 17 0 0 1 3 4a1 1 0 0 1 1-1h3.5a1 1 0 0 1 1 1c0 1.25.2 2.45.57 3.6a1 1 0 0 1-.25 1z"/></svg>
        +919812345670
      </li>
      <li>
        <svg viewBox="0 0 24 24" aria-hidden="true"><path d="M2 5h20v14H2z M2 5l10 8 10-8" /><path d="M2 5l10 8 10-8" fill="#fff"/></svg>
        rvashist@vexalund.com
      </li>
      <li>
        <svg viewBox="0 0 24 24" aria-hidden="true"><circle cx="12" cy="12" r="10"/><path d="M7 8c2 0 3 1 3 3s2 2 2 4-1 3-2 4M15 5c-1 2 0 3 2 3s3 2 3 3" stroke="#fff" stroke-width="1.6" fill="none"/></svg>
        https://vexalund.com
      </li>
    </ul>
    <address class="address">12, Neelkamal Colony, Nashik,<br>422001, India</address>

    <span class="brand-dot"></span>
    <p class="brand-name">Vexalund</p>
  </section>
</main>
</body>
</html>
```